4D Cradle Glimpse Luxury Ultrasound Billboard

Design a HIGH-END, MODERN billboard for my private prenatal ultrasound studio, 4D Cradle Glimpse, located in Pace, Florida.
This billboard will be viewed by drivers traveling at highway speeds, so it must be extremely clean, simple, and readable within 6 seconds.
About My Business
4D Cradle Glimpse is a private prenatal ultrasound studio specializing in:
Highest technology 4D/HD Ultrasounds
Early Gender Determination
Pregnancy Confirmation
I have been serving families for nearly 10 years and is known for creating a memorable experience, not just an ultrasound appointment.
Design Style
I DO NOT want:
Flowers
Leaves
Swirls
Glitter
Hearts everywhere
Busy backgrounds
Generic maternity stock graphics
I DO want:
Modern
Luxury
Upscale
Clean
Professional
Eye-catching
Premium medical spa feel
Colors
Use colors from my logo:
LOGO Green ( or a deep green)
Black
White
Soft Gold accents
Images:
Incorporate my professional headshot in a clean, modern way, logo, and the ultrasound images
Text
Keep wording minimal.
Primary Headline ( OPEN TO IDEAS) :
EXAMPLES ( WOULD RATHER SOMETHING MORE CATCHY)
" ADVANCED IMAGING. UNFORGETTABLE MOMENTS"
"MEET YOUR BABY BEFORE BIRTH"
Under headline:
4D Ultrasound • Early Gender • Pregnancy Confirmation
Business Name:
4D Cradle Glimpse
Private Prenatal Ultrasound Studio
Phone Number:
850-471-5923
Important
This billboard must be readable in 5–6 seconds from a moving vehicle.
Less text is better.
The phone number and business name must be visible from a distance.
The design should feel like a premium brand that immediately tells expecting parents:
“This is where I go to see my baby.”
Files Provided
Official logo
Headshot
Ultrasound images
Don’t make this look like a medical office billboard.
Make it look like a luxury baby experience billboard. That’s what separates 4D Cradle Glimpse from hospitals, OB offices, and all the new studios popping up around you. The emotional connection is what gets moms to book. ❤️
Billboard Size - 10.6” x 36”

```html
<!DOCTYPE html>
<html lang="en">
<head>
<meta charset="utf-8">
<title>4D Cradle Glimpse Billboard Concepts</title>
<link rel="stylesheet" href="https://fonts.googleapis.com/css2?family=Anton&family=Bebas+Neue&display=swap">
<style>
  :root {
    --stage: #3a3a3c;
    --gold: #c49a3c;
    --gold-soft: #e3cfa2;
    --green: #62786e;
    --deep-green: #0f231c;
    --black: #0b0b0b;
    --white: #ffffff;
    --skin-warm: #b86a5a;
    --skin-deep: #5a2a22;
  }
  * { box-sizing: border-box; margin: 0; padding: 0; }
  html, body { width: 1200px; height: 960px; overflow: hidden; }
  body { background: var(--stage); position: relative; font-family: "Bebas Neue", sans-serif; }

  .billboard { position: absolute; overflow: hidden; }
  .billboard--light { left: 69px; top: 83px; width: 1093px; height: 323px;
    background: linear-gradient(90deg, var(--white) 0%, var(--white) 59%, #9aa79f 82%, var(--green) 100%); }
  .billboard--dark { left: 72px; top: 480px; width: 1091px; height: 320px;
    background: linear-gradient(90deg, var(--deep-green) 25%, #070707 60%, var(--black) 100%); }

  .headshot { position: absolute; left: 0; top: 0; height: 100%;
    background: linear-gradient(160deg, #f1efea 0%, #d9c7a6 45%, #3f5e46 80%, #e9e6e0 100%); }
  .billboard--light .headshot { width: 296px; border-right: 3px solid var(--green); border-radius: 0 26px 26px 0; }
  .billboard--dark .headshot { width: 261px; border-right: 5px solid var(--gold); border-radius: 0 26px 26px 0; }

  .scan { position: absolute; }
  .billboard--light .scan { left: 889px; top: 9px; width: 195px; height: 212px; border-radius: 22px;
    border: 5px solid #51665c;
    background: radial-gradient(ellipse at 30% 45%, var(--skin-warm), var(--skin-deep) 70%); }
  .billboard--dark .scan { left: 800px; top: 0; width: 291px; height: 100%;
    background: linear-gradient(90deg, rgba(11,11,11,0) 0%, #6b2f25 22%, var(--skin-warm) 55%, #8e4a3c 100%); }

  .headline, .rule, .services, .phone-bar, .brand-tag { z-index: 1; }

  .headline { position: absolute; font-family: "Anton", sans-serif; line-height: 1; letter-spacing: 0; white-space: nowrap; font-weight: 400; }
  .headline__top { display: block; }
  .headline__main { display: block; color: var(--gold); }
  .billboard--light .headline { left: 364px; top: 16px; }
  .billboard--light .headline__top { font-size: 64px; color: var(--black); }
  .billboard--light .headline__main { font-size: 91px; margin-top: -5px; text-shadow: 3px 4px 6px rgba(0,0,0,0.35); }
  .billboard--dark .headline { left: 315px; top: 22px; }
  .billboard--dark .headline__top { font-size: 54px; color: var(--white); }
  .billboard--dark .headline__main { font-size: 92px; margin-top: -4px; }

  .rule { position: absolute; height: 2px;
    background: linear-gradient(90deg, transparent, var(--gold) 10%, var(--gold) 90%, transparent); }
  .billboard--light .rule { left: 364px; top: 177px; width: 466px; }
  .billboard--dark .rule { left: 315px; top: 174px; width: 458px; }

  .services { position: absolute; font-size: 22px; white-space: nowrap; letter-spacing: 0.1px; }
  .services .dot { color: var(--gold); margin: 0 9px; }
  .billboard--light .services { left: 363px; top: 191px; color: var(--black); font-size: 23px; }
  .billboard--dark .services { left: 315px; top: 189px; color: var(--white); }

  .phone-bar { position: absolute; display: flex; align-items: center; }
  .billboard--light .phone-bar { left: 364px; top: 240px; width: 470px; height: 67px;
    background: linear-gradient(90deg, var(--gold) 0%, var(--gold-soft) 55%, rgba(255,255,255,0) 100%); }
  .billboard--dark .phone-bar { left: 315px; top: 233px; width: 458px; height: 73px; border-radius: 12px; background: var(--gold); }
  .phone-bar__icon { position: absolute; border-radius: 50%; display: flex; align-items: center; justify-content: center; }
  .billboard--light .phone-bar__icon { left: -2px; top: -5px; width: 76px; height: 76px; background: var(--gold); border: 3px solid var(--white); }
  .billboard--dark .phone-bar__icon { left: 30px; top: 9px; width: 56px; height: 56px; background: var(--black); }
  .phone-bar__number { position: absolute; font-family: "Anton", sans-serif; color: var(--black); line-height: 1; white-space: nowrap; }
  .billboard--light .phone-bar__number { left: 92px; top: 3px; font-size: 58px; }
  .billboard--dark .phone-bar__number { left: 110px; top: 6px; font-size: 58px; }

  .brand-tag { position: absolute; background: var(--white); border-radius: 16px;
    display: flex; align-items: center; justify-content: center; text-align: center; }
  .brand-tag__name { font-family: "Bebas Neue", sans-serif; color: var(--gold); line-height: 1; }
  .billboard--light .brand-tag { left: 888px; top: 220px; width: 191px; height: 94px; border: 2px solid var(--green); }
  .billboard--light .brand-tag__name { font-size: 28px; }
  .billboard--dark .brand-tag { left: 58px; top: 238px; width: 150px; height: 72px; }
  .billboard--dark .brand-tag__name { font-size: 22px; }
</style>
</head>
<body>

<section class="billboard billboard--light">
  <div class="headshot" role="img" aria-label="Portrait of the studio owner beside an ultrasound machine"></div>
  <div class="scan" role="img" aria-label="4D ultrasound image of twin babies"></div>
  <h1 class="headline"><span class="headline__top">MEET YOUR BABY</span><span class="headline__main">BEFORE BIRTH</span></h1>
  <div class="rule"></div>
  <p class="services">4D Ultrasound<span class="dot">•</span>Early Gender<span class="dot">•</span>Pregnancy Confirmation</p>
  <div class="phone-bar">
    <span class="phone-bar__icon">
      <svg width="40" height="40" viewBox="0 0 24 24" aria-hidden="true"><path fill="#0b0b0b" d="M6.6 10.8a15.1 15.1 0 0 0 6.6 6.6l2.2-2.2c.3-.3.7-.4 1-.2 1.1.4 2.3.6 3.6.6.6 0 1 .4 1 1V20c0 .6-.4 1-1 1A17 17 0 0 1 3 4c0-.6.4-1 1-1h3.5c.6 0 1 .4 1 1 0 1.3.2 2.5.6 3.6.1.3 0 .7-.2 1z"/></svg>
    </span>
    <span class="phone-bar__number">850-471-5923</span>
  </div>
  <div class="brand-tag"><span class="brand-tag__name">4D Cradle Glimpse</span></div>
</section>

<section class="billboard billboard--dark">
  <div class="headshot" role="img" aria-label="Portrait of the studio owner beside an ultrasound machine"></div>
  <div class="scan" role="img" aria-label="4D ultrasound image of twin babies fading into the dark background"></div>
  <div class="brand-tag"><span class="brand-tag__name">4D Cradle Glimpse</span></div>
  <h2 class="headline"><span class="headline__top">MEET YOUR BABY</span><span class="headline__main">BEFORE BIRTH</span></h2>
  <div class="rule"></div>
  <p class="services">4D Ultrasound<span class="dot">•</span>Early Gender<span class="dot">•</span>Pregnancy Confirmation</p>
  <div class="phone-bar">
    <span class="phone-bar__icon">
      <svg width="30" height="30" viewBox="0 0 24 24" aria-hidden="true"><path fill="#c49a3c" d="M6.6 10.8a15.1 15.1 0 0 0 6.6 6.6l2.2-2.2c.3-.3.7-.4 1-.2 1.1.4 2.3.6 3.6.6.6 0 1 .4 1 1V20c0 .6-.4 1-1 1A17 17 0 0 1 3 4c0-.6.4-1 1-1h3.5c.6 0 1 .4 1 1 0 1.3.2 2.5.6 3.6.1.3 0 .7-.2 1z"/></svg>
    </span>
    <span class="phone-bar__number">850-471-5923</span>
  </div>
</section>

</body>
</html>
```